Local Flower Farm Needs Business Card Design

I need business cards designed for a flower farm based in Eudora, Kansas.
Business Info:
We are a local cut flower farm located in Eudora, Kansas, founded by Corinne Haldwick. What started as a passion for agriculture and search for more joy in daily life has blossomed into a small business dedicated to providing the community with beautiful, fresh, and sustainable flowers. We specialize in local, seasonal blooms, ensuring that every petal reflects the care and dedication we pour into our craft. Our mission is to deliver the highest quality flowers directly to our customers through local farmers markets and to florists who share our commitment to sustainability. Join us in celebrating the beauty of nature, one bloom at a time!
Contact Details:
Corinne Haldwick
Owner
Phone 913-555-0147
Facebook: Rosalind Thorpe Gardens
Instagram: @RosalindThorpeGardens
Website: RosalindThorpeGardens.example
Target Market(s)
Wholesale to Florists and Direct to Consumer via Farmers Market
Industry/Entity Type
Florist, Farm
Contact Information for Business Card
Name, Contact Info, Logo
Look and feel
Each slider illustrates characteristics of the customer's brand and the style your logo design should communicate.

```html
<!DOCTYPE html>
<html lang="en">
<head>
<meta charset="utf-8">
<title>Rosalind Thorpe Gardens – Business Card</title>
<link rel="stylesheet" href="https://fonts.googleapis.com/css2?family=Montserrat:wght@400;700&display=swap">
<style>
  :root {
    --ink: #07232a;
    --paper: #ececec;
    --paper-shade: #e2e2e2;
    --backdrop: #d8dbda;
    --light-text: #e6e6e6;
  }
  * { margin: 0; padding: 0; box-sizing: border-box; }
  html, body { width: 1200px; height: 1200px; overflow: hidden; }
  body {
    background: var(--backdrop);
    font-family: "Montserrat", Arial, sans-serif;
    position: relative;
  }
  .card {
    position: absolute;
    left: 130px;
    width: 940px;
    height: 537px;
    border-radius: 6px;
    overflow: hidden;
  }
  .card-front { top: 43px; background: linear-gradient(135deg, var(--paper), var(--paper-shade)); }
  .card-back { top: 620px; background: var(--ink); }

  .side-band {
    position: absolute; left: 0; top: 0; bottom: 0; width: 88px;
    background: var(--ink);
    display: flex; flex-direction: column; align-items: center;
    padding-top: 60px; gap: 14px;
  }
  .social-dot {
    width: 28px; height: 28px; border-radius: 50%;
    background: var(--light-text);
    flex: none;
  }
  .side-handle {
    writing-mode: vertical-rl;
    color: var(--light-text);
    font-size: 21px;
    letter-spacing: 0.3px;
  }

  .owner { position: absolute; left: 165px; top: 74px; color: var(--ink); }
  .owner-name { font-weight: 700; font-size: 30px; line-height: 1.1; }
  .owner-role { font-size: 22px; color: #33474b; margin-top: 4px; }

  .contact-list {
    position: absolute; left: 165px; top: 356px;
    list-style: none; color: var(--ink);
    font-size: 23px; line-height: 1.2;
  }
  .contact-list li { display: flex; align-items: center; gap: 12px; height: 36px; }
  .contact-list svg { width: 20px; height: 20px; flex: none; }

  .brand-seal {
    position: absolute;
    border-radius: 50%;
    display: flex; align-items: center; justify-content: center;
    text-align: center;
    font-family: "Montserrat", Arial, sans-serif;
    font-weight: 400;
    letter-spacing: 2px;
    text-transform: uppercase;
  }
  .card-front .brand-seal {
    left: 654px; top: 76px; width: 208px; height: 208px;
    border: 1px solid var(--ink); color: var(--ink); font-size: 19px; line-height: 1.35;
  }
  .card-back .brand-seal {
    left: 327px; top: 125px; width: 286px; height: 286px;
    border: 1px solid var(--light-text); color: var(--light-text); font-size: 25px; line-height: 1.4;
  }

  .back-handle {
    position: absolute; left: 0; right: 0; top: 456px;
    display: flex; justify-content: center; align-items: center; gap: 14px;
    color: var(--light-text); font-size: 24px;
  }
</style>
</head>
<body>
  <section class="card card-front">
    <aside class="side-band">
      <span class="social-dot"></span>
      <span class="side-handle">@RosalindThorpeGardens</span>
    </aside>

    <div class="owner">
      <p class="owner-name">Corinne Haldwick</p>
      <p class="owner-role">Owner</p>
    </div>

    <div class="brand-seal">Rosalind<br>Thorpe<br>Gardens</div>

    <ul class="contact-list">
      <li>
        <svg viewBox="0 0 24 24"><path fill="#07232a" d="M6.6 10.8a15.1 15.1 0 0 0 6.6 6.6l2.2-2.2a1 1 0 0 1 1-.25 11.4 11.4 0 0 0 3.6.57 1 1 0 0 1 1 1V20a1 1 0 0 1-1 1A17 17 0 0 1 3 4a1 1 0 0 1 1-1h3.5a1 1 0 0 1 1 1c0 1.25.2 2.45.57 3.57a1 1 0 0 1-.25 1z"/></svg>
        913-555-0147
      </li>
      <li>
        <svg viewBox="0 0 24 24"><path fill="#07232a" d="M2 5h20v14H2z"/><path fill="none" stroke="#ececec" stroke-width="1.6" d="M2.5 6l9.5 7 9.5-7"/></svg>
        corinne@rosalindthorpegardens.example
      </li>
      <li>
        <svg viewBox="0 0 24 24"><circle cx="12" cy="12" r="9.5" fill="none" stroke="#07232a" stroke-width="2"/><path fill="none" stroke="#07232a" stroke-width="1.6" d="M2.5 12h19M12 2.5c-3.5 4-3.5 15 0 19M12 2.5c3.5 4 3.5 15 0 19"/></svg>
        www.rosalindthorpegardens.example
      </li>
    </ul>
  </section>

  <section class="card card-back">
    <div class="brand-seal">Rosalind<br>Thorpe<br>Gardens</div>
    <p class="back-handle"><span class="social-dot"></span>@RosalindThorpeGardens</p>
  </section>
</body>
</html>
```